Business Card Design

We provide services doing multiple jobs in the construction industry.Please note: The company name needs to be ROCK SOLID BUILDING SERVICESAttached logo was an example of what we wanted. Can you change up the colors?

Industry/Entity Type

Construction

Contact Information for Business Card

ROCK SOLID BUILDING SERVICES5401 HUDSON BEND RDAUSTIN, TX 78734(512)243-6854ROCKSOLIDBUILDINGSERVICES@GMAIL.COM

```html
<!DOCTYPE html>
<html lang="en">
<head>
<meta charset="utf-8">
<title>Pearlwood Framing Works – Business Card</title>
<link rel="stylesheet" href="https://fonts.googleapis.com/css2?family=Arimo:wght@400;700&display=swap">
<style>
  :root {
    --backdrop: #d9d4cc;
    --card-white: #ffffff;
    --card-black: #050505;
    --slate: #5f7b92;
    --ink: #0b0b0b;
    --navy: #1d2f5e;
    --contact-text: #f2f2f2;
  }
  * { margin: 0; padding: 0; box-sizing: border-box; }
  html, body {
    width: 1200px; height: 800px; overflow: hidden;
    background: var(--backdrop);
    font-family: "Arimo", Arial, sans-serif;
  }
  .canvas {
    position: relative; width: 1200px; height: 800px;
    display: flex; align-items: center; justify-content: center;
  }
  .business-card {
    position: relative; width: 1000px; height: 572px;
    background: var(--card-black);
    box-shadow: 0 12px 30px rgba(0,0,0,.35);
    overflow: hidden;
  }
  .card-top {
    position: absolute; left: 0; top: 0; width: 100%; height: 300px;
    background: var(--card-white);
  }
  .brand-mark {
    position: absolute; left: 250px; top: 78px;
    display: flex; align-items: center; gap: 26px;
  }
  .brand-dot {
    width: 120px; height: 120px; border-radius: 50%;
    background: var(--slate); flex: none;
  }
  .brand-name {
    font-weight: 700; color: var(--ink);
    font-size: 44px; line-height: 1.05; letter-spacing: 0.5px;
  }
  .partner-mark {
    position: absolute; right: 48px; top: 205px;
    display: flex; align-items: center; gap: 14px;
  }
  .partner-square {
    width: 44px; height: 44px; background: var(--navy); flex: none;
  }
  .partner-name {
    font-weight: 700; color: var(--navy); font-size: 26px; letter-spacing: 0.5px;
  }
  .contact-list {
    position: absolute; left: 70px; top: 350px;
    list-style: none; color: var(--contact-text);
    font-size: 25px; letter-spacing: 1px;
  }
  .contact-item {
    display: flex; align-items: center; gap: 22px; margin-bottom: 24px;
  }
  .contact-icon { width: 26px; height: 22px; flex: none; fill: var(--contact-text); }
</style>
</head>
<body>
<main class="canvas">
  <article class="business-card">
    <section class="card-top">
      <div class="brand-mark">
        <span class="brand-dot"></span>
        <h1 class="brand-name">PEARLWOOD<br>FRAMING WORKS</h1>
      </div>
      <div class="partner-mark">
        <span class="partner-square"></span>
        <span class="partner-name">PEARLWOOD PIPEWORKS</span>
      </div>
    </section>
    <ul class="contact-list">
      <li class="contact-item">
        <svg class="contact-icon" viewBox="0 0 26 22" aria-hidden="true">
          <path d="M2 6 Q13 -1 24 6 L21 9 Q13 5 5 9 Z"/>
          <rect x="6" y="10" width="14" height="10" rx="2"/>
        </svg>
        <span>(512)555-0193</span>
      </li>
      <li class="contact-item">
        <svg class="contact-icon" viewBox="0 0 26 22" aria-hidden="true">
          <path d="M13 1 L25 11 L22 11 L22 21 L16 21 L16 14 L10 14 L10 21 L4 21 L4 11 L1 11 Z"/>
        </svg>
        <span>7732 FERNGLEN PASS LN AUSTIN, TX 78734</span>
      </li>
      <li class="contact-item">
        <svg class="contact-icon" viewBox="0 0 26 22" aria-hidden="true">
          <path d="M1 3 H25 V19 H1 Z M3 5 L13 12 L23 5" fill="none" stroke="#f2f2f2" stroke-width="2"/>
        </svg>
        <span>PEARLWOODFRAMINGWORKS@MAILNEST.EXAMPLE</span>
      </li>
    </ul>
  </article>
</main>
</body>
</html>
```